A Brochure to sell LED Downlights to clients

I am starting a campaign on google for LED down lights the link to the landing page can be found at brinholt.com.au/led .

When the client send a contact request i want to be able to send back a brochure of a picture of each light (Approx 6 - 8 types) and have a few sentences on each light and price brake down.

'Quarnel Ostrava 9w LED'

**Information**

1-10 lights $49
11-20 lights $45
21 - 40 lights $42
40 and over $40

EACH LIGHT:

Hi,

This is very good.

I
But,

Each light will have its own price.

Can i get it made like this;

Picture - Spec - Pricing in a table style please? - i like the layout it just need to suit the tables under:

picture - Brand - Price 1-10
Model - Price 11-20
Watts - Price 21-21
lumen - price 30- 40
Warranty = price 40+

Model - Price 11-20
Watts - Price 21-21
lumen - price 30- 40
Warranty = price 40+

Model - Price 11-20
Watts - Price 21-21
lumen - price 30- 40
Warranty = price 40+

and so on....

I want it to be on Microsoft Word so i can easily chop and edit the prices and images also. (So i can print to PDF)

For more information see my website to seek inspiration. I have a zip file of my logo for actual creation and should be also to source pictures of the lights when finalising the design.

brinholt.com.au

Thanks

Added 2 x additional Dimmers please see zip file, same layout/pricing as the downlights

Target Market(s)

Homeowners/commercial business owners

Industry/Entity Type

Electric Company

Font styles to use
Sans Serif

Colors
86cfc6
ffffff
000000

Requirements
Must have
• Professional looking, Colours to the theme of my logo/website
Nice to have
• An awesome design that sells it's self!!!!!!!
• My Logo font is 'Radikil" it would be nice to follow that theme if it doesn't look good i am open to have a nice legible font for the copy.
Should not have
• Cheesy light globes or images

```html
<!DOCTYPE html>
<html lang="en">
<head>
<meta charset="utf-8">
<title>Brinholt Electrical – LED Downlight Catalog</title>
<link rel="stylesheet" href="https://fonts.googleapis.com/css2?family=Josefin+Sans:wght@300;400;600;700&family=Questrial&display=swap">
<style>
  :root {
    --teal: #16a393;
    --teal-soft: #86cfc6;
    --charcoal: #414142;
    --white: #ffffff;
    --ink: #333333;
    --muted: #555555;
    --backdrop: #c8c8c8;
    --page-grey: #ececec;
  }
  * { box-sizing: border-box; margin: 0; padding: 0; }
  html, body { width: 1200px; height: 2980px; overflow: hidden; }
  body {
    background: var(--backdrop);
    position: relative;
    font-family: "Questrial", "Helvetica Neue", Arial, sans-serif;
    color: var(--ink);
  }
  .page {
    position: absolute;
    left: 292px;
    width: 626px;
    height: 884px;
    overflow: hidden;
    box-shadow: 4px 6px 10px rgba(0,0,0,0.35);
  }
  .heading-font { font-family: "Josefin Sans", "Century Gothic", sans-serif; }

  /* ---------- Cover ---------- */
  .cover { top: 118px; background: var(--white); }
  .cover__photo {
    position: absolute; left: 0; top: 0; width: 100%; height: 692px;
    background:
      radial-gradient(ellipse 120px 150px at 72% 78%, #3c5f9a 0%, #2d4a7c 60%, rgba(45,74,124,0) 100%),
      linear-gradient(180deg, #ffffff 0%, #ffffff 20%, #f3efe9 34%, #e8e1d6 50%, #ddd4c6 66%, #b9ad9c 84%, #7d7466 100%);
  }
  .cover__title {
    position: absolute; top: 44px; width: 100%; text-align: center;
    font-family: "Josefin Sans", "Century Gothic", sans-serif;
  }
  .cover__title-main {
    display: block; color: var(--teal); font-weight: 700;
    font-size: 66px; letter-spacing: 2px; line-height: 64px;
  }
  .cover__title-sub {
    display: inline-block; margin-top: 4px; border: 2px solid #666;
    padding: 8px 6px 0; font-size: 54px; line-height: 50px; color: #444;
    font-weight: 300; letter-spacing: 1px;
  }
  .cover__stripe { position: absolute; left: 0; top: 692px; width: 100%; height: 12px; background: var(--teal); }
  .cover__footer { position: absolute; left: 0; top: 704px; width: 100%; height: 180px; background: var(--charcoal); }
  .brand-name { font-family: "Questrial", Arial, sans-serif; color: var(--white); line-height: 1; }
  .cover__brand { position: absolute; left: 22px; top: 58px; display: flex; align-items: center; gap: 10px; }
  .cover__brand-mark { width: 20px; height: 20px; background: var(--teal); }
  .cover__brand .brand-name { font-size: 40px; }
  .cover__brand-sub { position: absolute; left: 56px; top: 104px; color: var(--white); font-size: 17px; letter-spacing: 2px; }
  .cover__url { position: absolute; right: 24px; bottom: 22px; color: var(--white); font-size: 25px; }

  /* ---------- Product page ---------- */
  .products { top: 1076px; background: var(--page-grey); }
  .products__backdrop {
    position: absolute; inset: 0;
    background: linear-gradient(180deg, #f5f5f5 0%, #e6e6e6 40%, #dedede 62%, #eeeeee 85%, #f3f3f3 100%);
  }
  .products__title {
    position: absolute; top: 30px; width: 100%; text-align: center;
    color: var(--teal); font-weight: 700; font-size: 31px; line-height: 42px; letter-spacing: 1px;
  }
  .product { position: absolute; width: 290px; }
  .product__image { width: 150px; height: 146px; border-radius: 14px; }
  .product__image--white {
    margin-left: 54px;
    background: radial-gradient(ellipse 62% 58% at 50% 52%, #ffffff 0%, #f7f7f7 42%, #d9d9d9 60%, #b7b7b7 70%, rgba(236,236,236,0) 78%);
  }
  .product__image--white-cable {
    margin-left: 30px;
    background:
      radial-gradient(ellipse 22% 18% at 78% 62%, #1e1e1e 0%, #2a2a2a 60%, rgba(236,236,236,0) 100%),
      radial-gradient(ellipse 52% 48% at 42% 50%, #ffffff 0%, #f4f4f4 46%, #d4d4d4 62%, #b0b0b0 70%, rgba(236,236,236,0) 78%);
  }
  .product__image--black {
    margin-left: 44px;
    background:
      radial-gradient(ellipse 34% 20% at 66% 76%, #1a1a1a 0%, #262626 60%, rgba(236,236,236,0) 100%),
      radial-gradient(ellipse 40% 36% at 36% 36%, #6b6b6b 0%, #3a3a3a 50%, #1c1c1c 72%, rgba(236,236,236,0) 80%);
  }
  .product__image--silver {
    margin-left: 30px;
    background: radial-gradient(ellipse 58% 48% at 50% 52%, #e4e0d8 0%, #c9c4b8 45%, #9a958a 62%, #6f6b62 70%, rgba(236,236,236,0) 78%);
  }
  .product__name {
    margin-top: 10px; color: var(--teal); font-size: 21px; font-weight: 400;
    font-family: "Josefin Sans", "Century Gothic", sans-serif;
  }
  .product__features { list-style: none; margin-top: 6px; }
  .product__features li {
    display: flex; align-items: center; gap: 12px;
    font-size: 11.5px; color: var(--muted); height: 23px;
  }
  .product__features li::before {
    content: ""; width: 12px; height: 12px; border-radius: 50%; background: var(--teal); flex: none;
  }
  .pricing {
    position: absolute; left: 28px; top: 718px; width: 576px; height: 118px;
    background: var(--charcoal); border: 4px solid var(--teal); border-radius: 22px;
  }
  .pricing__label {
    position: absolute; left: 188px; top: 702px; width: 250px; height: 30px;
    background: var(--teal); color: var(--white); text-align: center;
    font-size: 17px; line-height: 30px; z-index: 2;
  }
  .pricing__grid {
    position: absolute; left: 34px; top: 32px; right: 30px;
    display: grid; grid-template-columns: 1fr 1fr; row-gap: 8px;
    color: var(--white); font-size: 20px;
  }
  .pricing__grid .price { color: var(--teal-soft); }
  .pricing__grid > div:nth-child(even) { padding-left: 52px; }
  .products__url { position: absolute; right: 22px; bottom: 16px; font-size: 15px; color: var(--muted); }

  /* ---------- Back cover ---------- */
  .back { top: 2040px; background: var(--teal); }
  .back__strip { position: absolute; left: 0; top: 0; width: 100%; height: 12px; background: #7a7a7a; }
  .back__photo {
    position: absolute; left: 0; top: 12px; width: 100%; height: 872px;
    background: linear-gradient(180deg, #1fb3a3 0%, #17a494 40%, #128a7d 62%, #15998a 80%, #19a999 100%);
  }
  .back__brand { position: absolute; top: 290px; width: 100%; text-align: center; }
  .back__brand-mark { width: 18px; height: 18px; background: var(--white); margin: 0 auto 14px; }
  .back__brand .brand-name { font-size: 40px; }
  .back__brand-sub { color: var(--white); font-size: 17px; letter-spacing: 2px; margin-top: 4px; }
  .back__url { position: absolute; bottom: 34px; width: 100%; text-align: center; color: var(--white); font-size: 23px; }
</style>
</head>
<body>

<section class="page cover">
  <div class="cover__photo" role="img" aria-label="Photo of a retail shop interior lit by recessed LED downlights, with a bicycle displayed in an arched window"></div>
  <h1 class="cover__title">
    <span class="cover__title-main">PRODUCT</span>
    <span class="cover__title-sub">CATALOG</span>
  </h1>
  <div class="cover__stripe"></div>
  <footer class="cover__footer">
    <div class="cover__brand"><span class="cover__brand-mark"></span><span class="brand-name">brinholt</span></div>
    <div class="cover__brand-sub">Electrical</div>
    <div class="cover__url">brinholt.com.au</div>
  </footer>
</section>

<section class="page products">
  <div class="products__backdrop" role="img" aria-label="Faded photo of a room interior lit by downlights"></div>
  <h2 class="products__title heading-font">CHOOSE YOUR STYLE OF<br>LED DOWNLIGHTS</h2>

  <article class="product" style="left:24px; top:112px;">
    <div class="product__image product__image--white" role="img" aria-label="Photo of a white LED downlight fitting"></div>
    <h3 class="product__name">Lorem ipsum dolor</h3>
    <ul class="product__features">
      <li>Save 80% on your energy bills with LEDs</li>
      <li>50,000 hours of life</li>
      <li>Up to 7 years manufacturer's warranty</li>
      <li>Brighter than halogen downlights</li>
    </ul>
  </article>

  <article class="product" style="left:358px; top:112px;">
    <div class="product__image product__image--white-cable" role="img" aria-label="Photo of a white LED downlight with driver cable"></div>
    <h3 class="product__name">Lorem ipsum dolor</h3>
    <ul class="product__features">
      <li>Save 80% on your energy bills with LEDs</li>
      <li>50,000 hours of life</li>
      <li>Up to 7 years manufacturer's warranty</li>
      <li>Brighter than halogen downlights</li>
    </ul>
  </article>

  <article class="product" style="left:24px; top:412px;">
    <div class="product__image product__image--black" role="img" aria-label="Photo of a black gimbal LED downlight with driver"></div>
    <h3 class="product__name">Lorem ipsum dolor</h3>
    <ul class="product__features">
      <li>Save 80% on your energy bills with LEDs</li>
      <li>50,000 hours of life</li>
      <li>Up to 7 years manufacturer's warranty</li>
      <li>Brighter than halogen downlights</li>
    </ul>
  </article>

  <article class="product" style="left:358px; top:412px;">
    <div class="product__image product__image--silver" role="img" aria-label="Photo of a brushed silver LED downlight with spring clips"></div>
    <h3 class="product__name">Lorem ipsum dolor</h3>
    <ul class="product__features">
      <li>Save 80% on your energy bills with LEDs</li>
      <li>50,000 hours of life</li>
      <li>Up to 7 years manufacturer's warranty</li>
      <li>Brighter than halogen downlights</li>
    </ul>
  </article>

  <div class="pricing__label">Quarnel Ostrava 9w LED</div>
  <div class="pricing">
    <div class="pricing__grid">
      <div>1-10......lights : <span class="price">$49</span></div>
      <div>21-40...lights : <span class="price">$42</span></div>
      <div>11-20...lights : <span class="price">$45</span></div>
      <div>40 and over : <span class="price">$40</span></div>
    </div>
  </div>
  <div class="products__url">www.brinholt.com.au</div>
</section>

<section class="page back">
  <div class="back__strip"></div>
  <div class="back__photo" role="img" aria-label="Teal-tinted photo of a bedroom lit by ceiling downlights"></div>
  <div class="back__brand">
    <div class="back__brand-mark"></div>
    <div class="brand-name">brinholt</div>
    <div class="back__brand-sub">Electrical</div>
  </div>
  <div class="back__url">www.brinholt.com.au</div>
</section>

</body>
</html>
```